Cat-products company needs smart, yet endearing, business card

We need a business card design for a new, but up-and-running, business based in Honolulu, Hawaii. The business is Purrnest Nook Co. Our first product is the most environmentally-friendly cat grass kit ever seen on the planet. Future products, currently in the R&D phase, will include a variety of exciting cat scratchers. We also do consulting work to help apartment-dwellers make their home more cat-friendly and, in the future, plan on doing full, custom installs of structure to create high walkways for cats.

Target Market(s)

Middle-aged, apartment-dwelling, middle-class workers who own 1 or more cats and who dote on them.

Industry/Entity Type

Pet Care

Contact Information for Business Card

A striking, professional, yet warm and friendly design is what we're after.

Font styles to use
Serif
Sans Serif
Other font styles liked:
• Comfortaa

Colors

Designer to choose colors to be used in the design.

Requirements
Must have
• The company logo: (see attachment)
• The company name: Purrnest Nook Co
• The web address: www.purrnestnookco.com
• Email: support@purrnestnookco.com
• Phone: +1 (808) 571 6023
• Update (Fri Jun 30 3017 7:45pm Hawaii Time) I would like, is possible, uploaded picture of the cat grass kit on the back of the card with some text along the lines of: Purrnest Nook Co - Maker Of The Leafiest Feline Sprout Set Yet
Nice to have
• A cat picture, cartoon, real or silhouette that illustrates cats in action and/or relaxing; ie using the apartment space to live, play and relax in and being well-contented.
• Most of the website is done in the font: Comfortaa. It might be nice to continue using this for brand consistency.
Should not have
• Hard-to-read fonts.

```html
<!DOCTYPE html>
<html lang="en">
<head>
<meta charset="utf-8">
<title>Purrnest Nook Co – Business Card</title>
<link rel="stylesheet" href="https://fonts.googleapis.com/css2?family=Jost:wght@400;500;700&family=Comfortaa:wght@700&display=swap">
<style>
  :root {
    --stage: #e9e7e4;
    --card: #ffffff;
    --brown: #5a3a33;
    --gold: #f7b21b;
    --ink: #4a4a4a;
    --rule: #b9b9b9;
  }
  * { margin: 0; padding: 0; box-sizing: border-box; }
  html, body { width: 1200px; height: 1000px; overflow: hidden; }
  body {
    background: var(--stage);
    font-family: "Jost", Arial, sans-serif;
    position: relative;
  }
  .card {
    position: absolute;
    left: 290px;
    width: 620px;
    height: 354px;
    background: var(--card);
    box-shadow: 0 10px 28px rgba(0,0,0,.18);
    overflow: hidden;
  }
  .card--front { top: 90px; }
  .card--back { top: 520px; }

  .brand {
    display: flex;
    align-items: center;
    gap: 12px;
  }
  .brand__mark {
    width: 22px; height: 22px;
    background: var(--brown);
    border-radius: 50%;
    flex: none;
  }
  .brand__name {
    font-family: "Jost", Arial, sans-serif;
    font-weight: 700;
    color: var(--brown);
    font-size: 32px;
    letter-spacing: .5px;
    white-space: nowrap;
  }
  .card--front .brand {
    position: absolute;
    left: 50%; top: 50%;
    transform: translate(-50%, -50%);
  }
  .card--back .brand {
    position: absolute;
    left: 40px; top: 150px;
  }
  .card--back .brand__name { font-size: 24px; }
  .card--back .brand__mark { width: 18px; height: 18px; }

  .divider {
    position: absolute;
    left: 295px; top: 60px;
    width: 1px; height: 190px;
    background: var(--rule);
  }
  .details {
    position: absolute;
    left: 322px; top: 58px;
    color: var(--ink);
  }
  .details__name {
    font-weight: 700;
    color: var(--gold);
    font-size: 27px;
    letter-spacing: .5px;
    line-height: 1;
  }
  .details__role {
    font-weight: 500;
    font-size: 13px;
    color: var(--ink);
    margin-top: 4px;
  }
  .details__address {
    font-size: 14px;
    line-height: 1.3;
    margin-top: 22px;
  }
  .contacts {
    list-style: none;
    margin-top: 20px;
    font-size: 14px;
    line-height: 1.45;
  }
  .contacts li { display: flex; align-items: center; gap: 10px; }
  .contacts svg { width: 12px; height: 12px; flex: none; }
  .contacts .accent { color: var(--gold); }

  .swoosh {
    position: absolute;
    left: 0; bottom: 0;
    width: 620px; height: 140px;
  }
</style>
</head>
<body>
  <section class="card card--front" aria-label="Business card front">
    <div class="brand">
      <span class="brand__mark"></span>
      <span class="brand__name">Purrnest Nook Co</span>
    </div>
  </section>

  <section class="card card--back" aria-label="Business card back">
    <div class="brand">
      <span class="brand__mark"></span>
      <span class="brand__name">Purrnest Nook Co</span>
    </div>
    <div class="divider"></div>
    <div class="details">
      <h1 class="details__name">LEILANI MOREAU</h1>
      <p class="details__role">Director</p>
      <p class="details__address">Your Street Address,<br>Honolulu, 1234</p>
      <ul class="contacts">
        <li>
          <svg viewBox="0 0 12 12" aria-hidden="true"><path fill="#f7b21b" d="M2.5 1l2 2.3-1.1 1.3c.7 1.5 2 2.8 3.5 3.5l1.3-1.1L10.5 9 9.3 11C5 10.8 1.2 7 1 2.7z"/></svg>
          +1 (808) 571 6023
        </li>
        <li>
          <svg viewBox="0 0 12 12" aria-hidden="true"><rect x="0.5" y="2" width="11" height="8" fill="#f7b21b"/><path d="M1 2.5l5 4 5-4" stroke="#fff" stroke-width="1" fill="none"/></svg>
          support@purrnestnookco.com
        </li>
        <li>
          <svg viewBox="0 0 12 12" aria-hidden="true"><circle cx="6" cy="6" r="5.5" fill="#f7b21b"/><path d="M0.8 6h10.4M6 .6c-2.4 3-2.4 7.8 0 10.8M6 .6c2.4 3 2.4 7.8 0 10.8" stroke="#fff" stroke-width=".8" fill="none"/></svg>
          www.<span class="accent">purrnestnookco</span>.com
        </li>
      </ul>
    </div>
    <svg class="swoosh" viewBox="0 0 620 140" preserveAspectRatio="none" aria-hidden="true">
      <path d="M0 140 L0 128 C180 128 420 90 620 0 L620 140 Z" fill="var(--gold)"/>
      <path d="M0 126 C180 126 420 88 620 -2" stroke="var(--brown)" stroke-width="3" fill="none"/>
      <path d="M0 128 C180 128 420 92 620 6 L620 0 C420 90 180 128 0 128 Z" fill="#fff"/>
    </svg>
  </section>
</body>
</html>
```